New Business Cards for Tormin Group

We need a new Business Card to compliment our new logo. We are a vibrant design, manufacture and install business providing recreation areas, public parks and Municipal spaces. We want business cards that are classy, modern and clean.

We have recently changed our logo, and are celebrating our 40th anniversary. We want business cards with a new modern design to reflect our status.

Target Market(s)

Customers

Contact Information for Business Card

We need all the details of our 3 offices as per the business card attached. Please disregard the old logo on the business card, the other three files show our new logo.

Requirements
Must have
• All info as per attached business card but with new logo.
Nice to have

```html
<!DOCTYPE html>
<html lang="en">
<head>
<meta charset="utf-8">
<title>Tormin Group – Business Card</title>
<link rel="stylesheet" href="https://fonts.googleapis.com/css2?family=Montserrat:wght@600;700&family=Open+Sans:wght@400&display=swap">
<style>
  :root {
    --backdrop: #5f5f5f;
    --card: #ffffff;
    --brand-red: #e8323c;
    --ink-dark: #3d3d3d;
    --ink-body: #5a5a5a;
    --ink-soft: #707070;
    --rule: #c9c9c9;
  }
  * { margin: 0; padding: 0; box-sizing: border-box; }
  html, body {
    width: 1200px; height: 1200px; overflow: hidden;
    background: var(--backdrop);
  }
  .card {
    position: absolute; left: 59px; top: 285px;
    width: 1082px; height: 630px;
    background: var(--card);
    font-family: "Open Sans", Arial, sans-serif;
    color: var(--ink-body);
  }
  .brand {
    position: absolute; left: 34px; top: 100px;
    display: flex; align-items: center; gap: 18px;
  }
  .brand-dot {
    width: 84px; height: 84px; border-radius: 50%;
    background: var(--brand-red);
  }
  .brand-name {
    font-family: "Montserrat", Arial, sans-serif;
    font-weight: 700; font-size: 40px; color: var(--ink-dark);
    letter-spacing: 0.5px;
  }
  .person {
    position: absolute; right: 36px; top: 78px;
    text-align: right;
  }
  .person-name {
    font-family: "Montserrat", Arial, sans-serif;
    font-weight: 700; font-size: 33px; color: var(--brand-red);
    line-height: 1;
  }
  .person-title {
    margin-top: 16px; font-size: 24px; color: var(--ink-dark); line-height: 1;
  }
  .person-contact {
    margin-top: 27px; font-size: 23px; line-height: 44px; color: var(--ink-soft);
  }
  .person-contact .label { color: var(--ink-dark); }
  .divider { position: absolute; left: 0; top: 0; }
  .website {
    position: absolute; right: 36px; top: 293px;
    font-size: 21px; color: #ffffff; line-height: 30px;
  }
  .office {
    position: absolute; top: 422px; text-align: right;
  }
  .office-head { right: 747px; }
  .office-dubai { right: 379px; }
  .office-qatar { right: 36px; top: 424px; }
  .office-name {
    font-family: "Montserrat", Arial, sans-serif;
    font-weight: 600; font-size: 25px; color: var(--ink-dark);
    line-height: 1; margin-bottom: 18px;
  }
  .office-line { font-size: 18.5px; line-height: 32px; color: var(--ink-soft); }
</style>
</head>
<body>
  <div class="card">
    <div class="brand">
      <div class="brand-dot"></div>
      <div class="brand-name">Tormin Group</div>
    </div>

    <div class="person">
      <div class="person-name">Rami Solens</div>
      <div class="person-title">Managing Partner</div>
      <div class="person-contact">
        <div><span class="label">Phone:</span> +971 (0)50 000 4821</div>
        <div><span class="label">Email:</span> rami@tormingroup.com</div>
      </div>
    </div>

    <svg class="divider" width="1082" height="340" viewBox="0 0 1082 340">
      <line x1="24" y1="330" x2="680" y2="330" stroke="var(--rule)" stroke-width="2"/>
      <polygon points="700,287 1082,287 1082,329 678,329" fill="var(--brand-red)"/>
    </svg>
    <div class="website">www.tormingroup.com</div>

    <div class="office office-head">
      <div class="office-name">Head Office</div>
      <div class="office-line">P.O. Box: 10482 Abu Dhabi. U.A.E</div>
      <div class="office-line">Tel No: +971 (0)2 5550184</div>
      <div class="office-line">Fax No: +971(0)2 5550185</div>
      <div class="office-line">Email: sales@tormingroup.com</div>
    </div>

    <div class="office office-dubai">
      <div class="office-name">Dubai Office</div>
      <div class="office-line">P.O. Box: 204417 Dubai, U.A.E</div>
      <div class="office-line">Tel No: +971 (0)4 555120</div>
      <div class="office-line">Fax No: +971(0)4 555121</div>
      <div class="office-line">Email: sales@tormingroup.com</div>
    </div>

    <div class="office office-qatar">
      <div class="office-name">Qater Office</div>
      <div class="office-line">P.O. Box: 30871 Doha, Qatter</div>
      <div class="office-line">Tel No: +974 40000318</div>
      <div class="office-line">Fax No: +974 40000319</div>
      <div class="office-line">Email: sales@tormingroup.com</div>
    </div>
  </div>
</body>
</html>
```